Trailhead Cove Website - Sell Outdoor product

We are a mom and pop company that just opened our website.

We need a fresh, professional, and nice looking website for our outdoor products. We sell hunting, camping, fishing, and hiking products/accessories to name a few. Some of these products are optics, gun safes, gun bi-pods and tripods, gun lights, hunting camera, tents, hearing protection, targets, fishing poles, and hiking backpacks to name a few.

Our current website is: http://www.trailheadcove-example.com . You'll see our logo on the website, and it is attached. We aren't married to this logo, so if the designer thinks they can modify it or even come up with a better design for the website, they are more than welcome to do so. We need someone with good images of their own (clip art and/or outdoor images) they can use if they need to for our website.

I also attached a idea I had in plandraw, but please don't think this is set in stone. It is just a very rough idea. You can also go to our bazarro site to see what we sell: www.bazarro-example.com/shops/k9qz311mrtxn4p . Right now we sell everything on Bazarro, but our website will just focus on outdoor product. So please make it an outdoor focused website. And you can be creative with some of the product category names. We also want to leave room for some parallel product in the future. Like garden tools, back yard furniture, and BBQs.

Our company also wants to include a deals section on the website. We will probably update it once a week or month. I have included what I did for a deal and accompanying images for it. Image is called Morvelid (And the main images are 01 and 02).

We also want to make sure the file is compatible with our current web-hosting company, https://www.hostlyne-example.com. So I included a webpage layout zip folder. If you have any questions, please contact me.

This is for a PSD and HTML/CSS webpage. If you have any artwork or images that you own and want to use them for the webpage, please do so.

Target Market(s)

The hunter, outdoors person, camper, hiker, and etc.

Industry/Entity Type

It Company

Coding

Coded - Design and coding required

Number of Pages Required

3 page

Requirements
Must have
• The main page. PSD and HTML/CSS file.
• The category page. PSD and HTML/CSS file
• The product display page. PSD and HTML/CSS file
• Please also use some images that you have or from the sites below:
• You can get free stock images for 7 days (20 per day) from this site:
• https://www.pixelvault-example.com/complimentary/PVXTRL/?utm_source=PVXTrialFT&utm_medium=cpc&utm_campaign=PVXTrialFT&gclid=QWRt5mnBkdTRZpLoWsePb7uVbQ
• Has 14 good sites:
• http://www.venturedesk-example.com/article/517293
• Here are the ones I like:
• https://clearshot-example.com/
• http://brightwide-example.com/
• http://www.sitebloom-example.com/free/nature
• http://www.pictorium-example.com/archive
• http://tinyframes-example.co/
• http://old.vintlens-example.co/search/hiking
• http://fetchpix.blogsite-example.com/
• http://rolvenpask-example.com/post/584920173645/download
• http://openimagevault-example.com/
• If there is a photographer listed on or next to the image, on the bottom lower corner of the image, please put the photographer's name.
Nice to have
• I would like to have an unsubscribe page. If the designer has any of their own images of the outdoor world, and they want to use them, please do. Just make the right graphic changes to make it look good.
Should not have
• Try and keep green color to a minimum.

```html
<!DOCTYPE html>
<html lang="en">
<head>
<meta charset="utf-8">
<title>Trailhead Cove – Outdoor Products</title>
<link href="https://fonts.googleapis.com/css2?family=Open+Sans:wght@400;600&family=Play:wght@400;700&display=swap" rel="stylesheet">
<style>
  :root{
    --page:#cecece;
    --hero-light:#c9c6c3;
    --hero-mid:#a79e95;
    --hero-dark:#7d7167;
    --accent:#f6b80c;
    --accent-deep:#e9a400;
    --ink:#111;
    --text:#3a3a3a;
    --white:#fff;
    --panel:#dadbdd;
    --photo:#b9bcc1;
    --dark-btn:#2a2a2a;
  }
  *{box-sizing:border-box;margin:0;padding:0}
  html,body{width:1043px;height:1200px;overflow:hidden}
  body{background:var(--page);font-family:"Open Sans",sans-serif;color:var(--text);position:relative}
  a{color:inherit;text-decoration:none}

  .hero-photo{position:absolute;left:0;top:0;width:1043px;height:640px;
    background:
      radial-gradient(ellipse 300px 260px at 450px 330px, #8b7c6f 0%, rgba(139,124,111,0) 100%),
      radial-gradient(ellipse 260px 300px at 300px 260px, #d8d3cd 0%, rgba(216,211,205,0) 100%),
      linear-gradient(90deg,var(--hero-light) 0%,var(--hero-mid) 55%,var(--hero-dark) 100%);}
  .hero-fade{position:absolute;left:0;top:480px;width:1043px;height:160px;
    background:linear-gradient(180deg,rgba(206,206,206,0),var(--page))}

  .utility{position:absolute;top:14px;left:55px;right:52px;font-size:11.5px;color:var(--white)}
  .utility .newsletter{text-decoration:underline;position:absolute;left:0}
  .utility .account{position:absolute;right:0;display:flex;gap:22px}

  .brand{position:absolute;top:84px;left:0;width:1043px;text-align:center;
    font-family:"Play",sans-serif;font-weight:700;font-size:34px;color:var(--accent);letter-spacing:1px}
  .brand-mark{display:inline-block;width:14px;height:14px;background:var(--accent);margin-right:10px;vertical-align:4px}

  .main-nav{position:absolute;top:196px;left:52px;width:939px;height:41px;border-bottom:1px solid rgba(255,255,255,.85)}
  .main-nav a{position:absolute;top:0;font-size:13px;color:var(--white);letter-spacing:.2px}
  .main-nav a.active{color:var(--accent)}
  .main-nav a.active::after{content:"";position:absolute;left:-10px;right:-3px;top:34px;height:4px;background:var(--accent)}

  .hero-copy{position:absolute;left:718px;top:298px;width:280px}
  .hero-title{font-family:"Play",sans-serif;font-size:52px;line-height:1;color:var(--accent);text-shadow:2px 3px 4px rgba(0,0,0,.35)}
  .hero-sub{font-family:"Play",sans-serif;font-size:28px;color:var(--ink);margin-top:2px}
  .hero-text{font-size:11.5px;line-height:14px;color:var(--white);margin-top:12px}
  .btn{display:inline-flex;align-items:center;justify-content:center;font-family:"Play",sans-serif;font-weight:700;
    color:#3a2a00;background:linear-gradient(180deg,var(--accent),var(--accent-deep));border-radius:2px;
    box-shadow:0 2px 3px rgba(0,0,0,.2)}
  .hero-copy .btn{width:109px;height:43px;font-size:14.5px;margin-top:24px}

  .slider-dots{position:absolute;top:560px;left:486px;display:flex;gap:20px}
  .slider-dots span{width:10px;height:10px;border-radius:50%;background:#bdbdbd}
  .slider-dots span.on{background:var(--accent)}

  .category-panel{position:absolute;left:52px;top:634px;width:242px;height:431px;background:var(--panel);
    box-shadow:0 1px 4px rgba(0,0,0,.12);border-radius:2px;padding-top:30px}
  .category-panel li{list-style:none;height:48px;display:flex;align-items:center;padding-left:24px;
    font-family:"Play",sans-serif;font-size:19px;color:#333}
  .category-panel svg{margin-right:14px}

  .section-title{position:absolute;left:330px;top:628px;font-family:"Play",sans-serif;font-weight:700;font-size:33px;color:var(--ink)}
  .carousel-nav{position:absolute;top:634px;left:919px;display:flex;gap:5px}
  .carousel-nav span{width:34px;height:34px;background:var(--dark-btn);display:flex;align-items:center;justify-content:center}

  .product{position:absolute;top:708px;width:204px}
  .product-frame{width:204px;height:216px;background:var(--white);padding:12px;box-shadow:0 1px 3px rgba(0,0,0,.1)}
  .product-photo{width:100%;height:100%;background:radial-gradient(ellipse at center,#5a5d62 0%,#5a5d62 22%,var(--photo) 60%)}
  .product-name{font-size:13px;line-height:15.5px;color:var(--text);margin:22px 0 0 3px;height:32px}
  .product-price{font-family:"Play",sans-serif;font-weight:700;font-size:15px;color:var(--ink);margin:11px 0 0 3px}
  .product-price s{margin-right:4px}
  .product .btn{width:109px;height:43px;font-size:14.5px;margin-top:16px;margin-left:-2px}

  .site-footer{position:absolute;left:52px;top:1116px;width:939px;border-top:1px solid #bcbcbc}
  .footer-links{position:absolute;top:22px;left:3px;font-size:11.5px;color:#333;white-space:nowrap}
  .footer-links span{margin:0 8px}
  .copyright{position:absolute;top:46px;left:3px;font-size:11.5px;color:#333}
  .help{position:absolute;top:21px;right:0;font-size:14.5px;font-weight:600;color:#333}
</style>
</head>
<body>
  <div class="hero-photo" role="img" aria-label="Close-up photograph of a grey wolf on a soft blurred background"></div>
  <div class="hero-fade"></div>

  <div class="utility">
    <a class="newsletter" href="#">Join Our Newsletter</a>
    <div class="account"><a href="#">My Account</a><span>|</span><a href="#">Login</a><span>|</span><a href="#">Shopping Cart</a></div>
  </div>

  <div class="brand"><span class="brand-mark"></span>TRAILHEAD COVE</div>

  <nav class="main-nav">
    <a class="active" href="#" style="left:52px">HOME</a>
    <a href="#" style="left:143px">HUNTINGACCESSORIES</a>
    <a href="#" style="left:344px">CAMPING</a>
    <a href="#" style="left:456px">FISHING</a>
    <a href="#" style="left:560px">HIKING</a>
    <a href="#" style="left:657px">THIS WEEKSDEALS</a>
    <a href="#" style="left:832px">BRANDS</a>
  </nav>

  <div class="hero-copy">
    <div class="hero-title">Hunting</div>
    <div class="hero-sub">Products</div>
    <p class="hero-text">Neque porro quisquam est, qui dolorem ipsum quia dolor sit amet, consectetur,</p>
    <a class="btn" href="#">Read More</a>
  </div>

  <div class="slider-dots"><span></span><span class="on"></span><span></span></div>

  <ul class="category-panel">
    <li><svg width="12" height="12" viewBox="0 0 12 12"><path d="M1 1l5 5-5 5M6 1l5 5-5 5" fill="none" stroke="#333" stroke-width="1.5"/></svg>Optics</li>
    <li><svg width="12" height="12" viewBox="0 0 12 12"><path d="M1 1l5 5-5 5M6 1l5 5-5 5" fill="none" stroke="#333" stroke-width="1.5"/></svg>Safes</li>
    <li><svg width="12" height="12" viewBox="0 0 12 12"><path d="M1 1l5 5-5 5M6 1l5 5-5 5" fill="none" stroke="#333" stroke-width="1.5"/></svg>Bipod and Tripods</li>
    <li><svg width="12" height="12" viewBox="0 0 12 12"><path d="M1 1l5 5-5 5M6 1l5 5-5 5" fill="none" stroke="#333" stroke-width="1.5"/></svg>Lights</li>
    <li><svg width="12" height="12" viewBox="0 0 12 12"><path d="M1 1l5 5-5 5M6 1l5 5-5 5" fill="none" stroke="#333" stroke-width="1.5"/></svg>Cameras</li>
    <li><svg width="12" height="12" viewBox="0 0 12 12"><path d="M1 1l5 5-5 5M6 1l5 5-5 5" fill="none" stroke="#333" stroke-width="1.5"/></svg>Tents</li>
    <li><svg width="12" height="12" viewBox="0 0 12 12"><path d="M1 1l5 5-5 5M6 1l5 5-5 5" fill="none" stroke="#333" stroke-width="1.5"/></svg>Ear Protection</li>
    <li><svg width="12" height="12" viewBox="0 0 12 12"><path d="M1 1l5 5-5 5M6 1l5 5-5 5" fill="none" stroke="#333" stroke-width="1.5"/></svg>Targets</li>
  </ul>

  <h2 class="section-title">New Products</h2>
  <div class="carousel-nav">
    <span><svg width="10" height="14" viewBox="0 0 10 14"><path d="M7 2L2 7l5 5" fill="none" stroke="#fff" stroke-width="1.6"/></svg></span>
    <span><svg width="10" height="14" viewBox="0 0 10 14"><path d="M3 2l5 5-5 5" fill="none" stroke="#fff" stroke-width="1.6"/></svg></span>
  </div>

  <article class="product" style="left:330px">
    <div class="product-frame"><div class="product-photo" role="img" aria-label="Black portable solar charger case with speaker"></div></div>
    <p class="product-name">Portable Solar Charger Case with Speaker</p>
    <p class="product-price"><s>$89.40</s> $60.78</p>
    <a class="btn" href="#">Add to Cart</a>
  </article>
  <article class="product" style="left:559px">
    <div class="product-frame"><div class="product-photo" role="img" aria-label="Black USB device charger with flashlight attachment"></div></div>
    <p class="product-name">Portable USB Device Charger with Flashlight Attachment</p>
    <p class="product-price"><s>$89.40</s> $60.78</p>
    <a class="btn" href="#">Add to Cart</a>
  </article>
  <article class="product" style="left:786px">
    <div class="product-frame"><div class="product-photo" role="img" aria-label="Heart rate monitor watch with chest strap"></div></div>
    <p class="product-name">Heart Rate Monitor Watch w/Calorie Counter...</p>
    <p class="product-price"><s>$89.40</s> $60.78</p>
    <a class="btn" href="#">Add to Cart</a>
  </article>

  <footer class="site-footer">
    <div class="footer-links"><a href="#">Home</a><span>/</span><a href="#">About us</a><span>/</span><a href="#">FAQ</a><span>/</span><a href="#">Blog</a><span>/</span><a href="#">Privacy</a><span>/</span><a href="#">Terms &amp; Conditions</a><span>/</span><a href="#">Shipping and Return</a></div>
    <p class="copyright">© 2015 Trailhead Cove LLC. All rights reserved</p>
    <p class="help">Need Help:(555) 014-2290</p>
  </footer>
</body>
</html>
```